Complete redesign of Licensed Medical Cannabis Dispensary website

Redesign website to modernize it and simplify it and add a self service reservation/preorder interactive delivery form. Also integrate current POS system that has current inventory. Here is a website for inspiration that I really like because of it simplicity https://www.leafroute.example and easy ordering option. Attached is our logo.... please design around that and this is our website address www.meadowcrestcourier.example

Font styles to use
Sans Serif

Colors
5c5c5c
cbcbcb
000000
add136

Requirements
Must have
• inventory thats integrated with pos
• online reservation/delivery form
Nice to have
• a website thats modern and simple
• The website designed are the logo that is attached
Should not have
• too much information

```html
<!DOCTYPE html>
<html lang="en">
<head>
<meta charset="utf-8">
<title>Meadowcrest Courier</title>
<link rel="stylesheet" href="https://fonts.googleapis.com/css2?family=Roboto+Condensed:wght@400;700&family=Roboto:wght@400;500;700&display=swap">
<style>
:root{
  --green:#add136;
  --green-dark:#6f9a1f;
  --green-deep:#4f7d14;
  --ink:#000000;
  --grey:#5c5c5c;
  --light:#cbcbcb;
  --paper:#ffffff;
  --mist:#efefef;
  --band:#4d4d4d;
}
*{box-sizing:border-box;margin:0;padding:0}
html,body{width:1200px;height:3651px;overflow:hidden}
body{position:relative;font-family:Roboto,sans-serif;color:var(--grey);background:var(--paper)}
.abs{position:absolute}
.head{font-family:"Roboto Condensed",sans-serif;font-weight:700;text-transform:uppercase}

/* header */
.site-header{left:0;top:0;width:1200px;height:97px;background:var(--paper)}
.brand{left:134px;top:26px;display:flex;align-items:center;gap:12px;font-family:Roboto,sans-serif;font-weight:700;font-size:24px;color:var(--green-deep)}
.brand-mark{width:34px;height:34px;border-radius:50%;background:var(--green-deep)}
.nav{right:141px;top:38px;display:flex;gap:28px;align-items:center;font-family:Roboto,sans-serif;font-weight:500;font-size:14px;color:#222;text-transform:uppercase}

/* hero */
.hero{left:0;top:97px;width:1200px;height:626px;background:linear-gradient(100deg,#3d6a1e 0%,#6f9a3a 35%,#d9dfd2 50%,#5f8b2c 70%,#2f5514 100%)}
.hero-title{left:134px;top:290px;font-size:52px;line-height:56px;color:var(--paper)}
.btn{display:flex;align-items:center;justify-content:center;background:var(--green);color:var(--paper);font-family:Roboto,sans-serif;font-weight:700;font-size:15px;text-transform:uppercase;border-radius:22px}
.hero-btn{left:134px;top:424px;width:158px;height:38px}
.dots{display:flex;gap:9px}
.dot{width:11px;height:11px;border-radius:50%;background:var(--paper)}
.dot.ring{background:transparent;border:2px solid var(--paper)}
.hero-dots{left:134px;top:488px}
.reserve{left:769px;top:207px;width:300px;height:377px;background:rgba(20,20,20,.82);color:var(--paper);text-align:center}
.reserve h2{margin-top:32px;font-size:24px}
.reserve p{font-family:"Roboto Condensed",sans-serif;font-weight:700;font-size:19px;margin-top:6px}
.field{position:absolute;left:29px;width:244px;height:38px;background:var(--paper);color:#333;font-size:11px;text-align:left;padding:12px 14px}
.field.select::after{content:"";position:absolute;right:14px;top:16px;border:5px solid transparent;border-top-color:#333}
.reserve .submit{position:absolute;left:29px;top:324px;width:244px;height:36px;border-radius:0;font-family:"Roboto Condensed",sans-serif;font-size:16px}

/* steps */
.steps{left:0;top:723px;width:1200px;height:506px;background:linear-gradient(180deg,#f5f7f2 0%,#e7ece0 60%,#dde5d3 100%)}
.step-text{position:absolute;width:250px;text-align:center;color:var(--paper)}
.step-text h3{font-family:"Roboto Condensed",sans-serif;font-weight:700;font-size:20px;text-transform:uppercase;margin-bottom:10px}
.step-text p{font-size:12.5px;line-height:18px}

/* cta band */
.cta{left:0;top:1229px;width:1200px;height:183px;background:var(--band)}
.cta p{position:absolute;left:260px;top:56px;font-size:22px;line-height:32px;color:var(--paper)}
.cta-btn{left:781px;top:1301px;width:159px;height:39px}

/* welcome */
.welcome{left:0;top:1412px;width:1200px;height:511px;background:var(--mist)}
.welcome-photo{left:176px;top:1485px;width:340px;height:340px;border-radius:50%;border:6px solid var(--green);background:radial-gradient(circle at 40% 40%,#f4f1ec,#cfc6b8 70%,#8a6b3e)}
.welcome h2{left:577px;top:1522px;font-size:32px;color:#1a1a1a}
.welcome-copy{left:577px;top:1584px;width:470px;font-size:13px;line-height:28px}
.more-btn{left:577px;top:1755px;width:122px;height:32px;background:var(--green-dark);text-transform:none;font-weight:500;font-size:14px}

/* products */
.section-title{width:1200px;left:0;text-align:center;font-size:36px;color:#1a1a1a}
.rule{left:570px;top:2093px;width:60px;height:3px;background:var(--green)}
.product{position:absolute;width:220px;text-align:center}
.product .shot{height:158px;margin:0 20px;background:radial-gradient(ellipse at center,#8f9a4e 0%,#b9b58e 40%,#fff 72%)}
.product h4{margin-top:28px;font-size:14.5px;line-height:24px;color:#333;font-weight:400;text-transform:uppercase}
.product .price{margin-top:8px;font-size:17px;font-weight:700;font-style:italic;color:var(--green-dark)}

/* testimonials */
.testimonials{left:0;top:2872px;width:1200px;height:407px;background:#f2f2f2}
.leaf{position:absolute;background:radial-gradient(circle,#5f9a1c 0%,rgba(95,154,28,.0) 70%)}
.quote{left:236px;top:3032px;width:728px;text-align:center;font-size:12.5px;line-height:25px;color:#555}
.quote-mark{font-family:Georgia,serif;font-size:34px;color:#333}
.author{left:0;width:1200px;top:3126px;text-align:center;font-size:16px;color:#333}
.author b{font-weight:500}
.t-dots{left:572px;top:3178px}
.t-dots .dot{width:13px;height:13px;background:var(--green)}
.t-dots .dot.ring{background:transparent;border:2px solid #888}

/* footer */
.footer{left:0;top:3279px;width:1200px;height:372px;background:linear-gradient(180deg,#5d9c21 0%,#7fb52e 50%,#5c9a1e 100%);color:var(--paper)}
.footer h5{font-family:"Roboto Condensed",sans-serif;font-weight:700;font-size:20px;text-transform:uppercase;position:absolute;top:68px}
.social{left:131px;top:3378px;display:flex;gap:8px}
.social span{width:30px;height:30px;background:rgba(255,255,255,.9)}
.emblem{left:140px;top:3440px;width:90px;height:90px;border-radius:50%;background:rgba(255,255,255,.35)}
.contact{left:331px;top:3385px;font-size:12.5px;line-height:18px}
.contact li{list-style:none;display:flex;gap:16px;margin-bottom:12px}
.contact svg{flex:none;margin-top:2px}
.links{position:absolute;top:106px;font-size:12.5px;line-height:24px;list-style:none}
.links li::before{content:"›";margin-right:14px}
.copyright{left:0;width:1200px;top:3597px;text-align:center;font-size:11.5px}
</style>
</head>
<body>

<header class="site-header abs">
  <div class="brand abs"><span class="brand-mark"></span>Meadowcrest Courier</div>
  <nav class="nav abs">
    <span>Home</span><span>Forums</span><span>Our Products</span><span>Edibles</span><span>Login/Sign Up</span><span>More</span>
    <svg width="18" height="18" viewBox="0 0 18 18"><circle cx="7.5" cy="7.5" r="5.5" fill="none" stroke="#4f7d14" stroke-width="2.5"/><path d="M11.5 11.5 16 16" stroke="#4f7d14" stroke-width="3"/></svg>
    <svg width="24" height="20" viewBox="0 0 24 20"><path d="M1 3h4l3 10h11l3-8H7" fill="none" stroke="#4f7d14" stroke-width="2.4"/><circle cx="10" cy="17" r="1.8" fill="#4f7d14"/><circle cx="18" cy="17" r="1.8" fill="#4f7d14"/><circle cx="20" cy="3" r="3" fill="#4f7d14"/></svg>
  </nav>
</header>

<section class="hero abs" role="img" aria-label="Smiling pharmacist in a white coat holding a clipboard in a cannabis grow room"></section>
<h1 class="hero-title head abs">Meadowcrest Courier<br>Delivery</h1>
<div class="hero-btn btn abs">Get Started</div>
<div class="hero-dots dots abs"><span class="dot ring"></span><span class="dot"></span><span class="dot"></span><span class="dot"></span></div>

<form class="reserve abs">
  <h2 class="head">Online Reservation</h2>
  <p>or Call us (555) 014-2280</p>
  <div class="field" style="top:119px">Name *</div>
  <div class="field" style="top:168px">Phone *</div>
  <div class="field" style="top:217px">Email *</div>
  <div class="field select" style="top:265px">Meadowcrest Courier</div>
  <div class="submit btn">Online Reservation</div>
</form>

<section class="steps abs">
  <svg class="abs" style="left:0;top:0" width="1200" height="506" viewBox="0 0 1200 506">
    <defs>
      <linearGradient id="stepFill" x1="0" y1="0" x2="1" y2="1">
        <stop offset="0" stop-color="#a8cf34"/><stop offset="1" stop-color="#5f9618"/>
      </linearGradient>
    </defs>
    <g>
      <path d="M263 95 A146 146 0 1 0 263 387 Q330 387 409 241 Q330 95 263 95 Z" fill="url(#stepFill)"/>
      <path d="M263 107 A134 134 0 1 0 263 375 Q322 375 396 241 Q322 107 263 107 Z" fill="none" stroke="#fff" stroke-width="2" stroke-dasharray="5 4"/>
    </g>
    <g>
      <path d="M597 95 A146 146 0 1 0 597 387 Q664 387 743 241 Q664 95 597 95 Z" fill="url(#stepFill)"/>
      <path d="M597 107 A134 134 0 1 0 597 375 Q656 375 730 241 Q656 107 597 107 Z" fill="none" stroke="#fff" stroke-width="2" stroke-dasharray="5 4"/>
    </g>
    <g>
      <path d="M932 95 A146 146 0 1 0 932 387 Q999 387 1078 241 Q999 95 932 95 Z" fill="url(#stepFill)"/>
      <path d="M932 107 A134 134 0 1 0 932 375 Q991 375 1065 241 Q991 107 932 107 Z" fill="none" stroke="#fff" stroke-width="2" stroke-dasharray="5 4"/>
    </g>
    <path d="M382 165 Q420 140 450 155" fill="none" stroke="#5f9618" stroke-width="2" stroke-dasharray="5 4"/>
    <path d="M444 148 452 156 442 160" fill="none" stroke="#5f9618" stroke-width="2"/>
    <path d="M712 345 Q745 360 775 350" fill="none" stroke="#5f9618" stroke-width="2" stroke-dasharray="5 4"/>
    <path d="M767 344 776 350 767 356" fill="none" stroke="#5f9618" stroke-width="2"/>
    <!-- icons -->
    <g fill="none" stroke="#fff" stroke-width="2.5">
      <path d="M226 160h28l10 10v38h-38z"/><path d="M233 176h20M233 186h20M233 196h12"/><circle cx="258" cy="202" r="8" fill="#8dbd2a"/><path d="M254 202l3 3 5-6"/>
      <path d="M580 160l17-14 17 14"/><path d="M572 164h50l-6 28h-38z"/><path d="M588 172v14M597 172v14M606 172v14"/>
      <rect x="918" y="148" width="28" height="18" rx="2"/><path d="M932 166v10M912 200a20 14 0 0 1 40 0v6h-40z"/><path d="M924 157h16M932 152v10"/>
    </g>
  </svg>
  <div class="step-text" style="left:118px;top:240px"><h3>Get Verified</h3><p>It's fast. It's simple. Just fill out our verification form and get approved in minutes.</p></div>
  <div class="step-text" style="left:462px;top:240px"><h3>Shop</h3><p>Add the products you want to your shopping cart and check out. No credit card required!</p></div>
  <div class="step-text" style="left:797px;top:240px"><h3>Get Medicated</h3><p>Sit back and wait. Our professional staff will deliver your medication right to your front door.</p></div>
</section>

<section class="cta abs">
  <p>Don't have your doctor's recommendation yet?<br>Get it online for just $49!</p>
</section>
<div class="cta-btn btn abs">Get Started</div>

<section class="welcome abs"></section>
<div class="welcome-photo abs" role="img" aria-label="Hand holding a medical cannabis bottle over spilled flower buds"></div>
<h2 class="head abs" style="left:577px;top:1522px;font-size:32px;color:#1a1a1a">Welcome to Meadowcrest Courier</h2>
<p class="welcome-copy abs">Sed ut perspiciatis unde omnis iste natus error sit voluptatem accusan-tium doloremque laudantium, totam rem aperiam, eaque ipsa quae ab illo inventore veritatis et quasi architecto beatae vitae dicta sunt explicabo. Nemo enim ipsam voluptatem quia voluptas sit aspernatur aut odit aut fugit, sed quia consequuntur magni dolores eos qui ratione</p>
<div class="more-btn btn abs">Read More</div>

<h2 class="section-title head abs" style="top:2027px">Flowers</h2>
<div class="rule abs"></div>

<div class="product" style="left:112px;top:2154px"><div class="shot" role="img" aria-label="Cannabis flower bud"></div><h4>Quis autem vel eum iure reprehenderit qui in</h4><div class="price">$15.59</div></div>
<div class="product" style="left:357px;top:2154px"><div class="shot" role="img" aria-label="Medicine jar with green capsules"></div><h4>Quis autem vel eum iure reprehenderit qui in</h4><div class="price">$15.59</div></div>
<div class="product" style="left:620px;top:2154px"><div class="shot" role="img" aria-label="Cannabis flower bud"></div><h4>Quis autem vel eum iure reprehenderit qui in</h4><div class="price">$15.59</div></div>
<div class="product" style="left:864px;top:2154px"><div class="shot" role="img" aria-label="Glass jar with buds and tincture bottle"></div><h4>Quis autem vel eum iure reprehenderit qui in</h4><div class="price">$15.59</div></div>

<div class="product" style="left:112px;top:2483px"><div class="shot" role="img" aria-label="Oil bottle beside a bowl of dried flower"></div><h4>Quis autem vel eum iure reprehenderit qui in</h4><div class="price">$15.59</div></div>
<div class="product" style="left:357px;top:2483px"><div class="shot" role="img" aria-label="Large cannabis bud"></div><h4>Quis autem vel eum iure reprehenderit qui in</h4><div class="price">$15.59</div></div>
<div class="product" style="left:620px;top:2483px"><div class="shot" role="img" aria-label="Glass of ground flower"></div><h4>Quis autem vel eum iure reprehenderit qui in</h4><div class="price">$15.59</div></div>
<div class="product" style="left:864px;top:2483px"><div class="shot" role="img" aria-label="Cannabis flower bud"></div><h4>Quis autem vel eum iure reprehenderit qui in</h4><div class="price">$15.59</div></div>

<section class="testimonials abs">
  <div class="leaf" style="left:-30px;top:20px;width:190px;height:190px" role="img" aria-label="Cannabis leaf decoration"></div>
  <div class="leaf" style="left:1040px;top:130px;width:190px;height:190px" role="img" aria-label="Cannabis leaf decoration"></div>
</section>
<h2 class="section-title head abs" style="top:2968px">Testimonials</h2>
<p class="quote abs"><span class="quote-mark">“</span> Lorem ipsum dolor sit amet, consectetur adipiscing elit, sed do eiusmod tempor incididunt ut labore et dolore magna aliqua. Ut enim ad minim veniam, quis nostrud exercitation ullamco laboris nisi ut aliquip ex ea commodo consequat. Duis aute irure dolor in reprehenderit in voluptate velit esse cillum dolore eu fugiat nulla pariatur. <span class="quote-mark">”</span></p>
<p class="author abs"><b>Jane Rowe</b> - Meadowcrest Courier</p>
<div class="t-dots dots abs"><span class="dot"></span><span class="dot ring"></span><span class="dot ring"></span></div>

<footer class="footer abs">
  <h5 style="left:131px">Follow Us</h5>
  <h5 style="left:331px">Contact Us</h5>
  <h5 style="left:633px">Explore</h5>
  <h5 style="left:859px">Forums</h5>
  <ul class="links" style="left:633px"><li>Store</li><li>Cart</li><li>My Account</li><li>New Patient Verification</li><li>Contact Us</li></ul>
  <ul class="links" style="left:859px"><li>Bongs, Bubblers, &amp; Water Pipes</li><li>Concentrates</li><li>Growing</li><li>Vaporizers</li><li>What Are You Smokin'?</li></ul>
</footer>
<div class="social abs" aria-label="Social links"><span></span><span></span><span></span></div>
<div class="emblem abs" role="img" aria-label="Medical emblem"></div>
<ul class="contact abs">
  <li><svg width="14" height="18" viewBox="0 0 14 18"><path d="M7 1a6 6 0 0 1 6 6c0 5-6 10-6 10S1 12 1 7a6 6 0 0 1 6-6z" fill="none" stroke="#fff" stroke-width="1.6"/><circle cx="7" cy="7" r="2" fill="#fff"/></svg><span>Meadowcrest Courier 41 Elm Row,<br>Fairhaven Valley</span></li>
  <li><svg width="16" height="16" viewBox="0 0 16 16"><path d="M3 1l3 3-2 2a9 9 0 0 0 6 6l2-2 3 3-2 2C7 15 1 9 1 3z" fill="none" stroke="#fff" stroke-width="1.5"/></svg><span>Phone : &nbsp;555 0190 4400</span></li>
  <li><svg width="16" height="12" viewBox="0 0 16 12"><rect x="1" y="1" width="14" height="10" fill="none" stroke="#fff" stroke-width="1.5"/><path d="M1 1l7 6 7-6" fill="none" stroke="#fff" stroke-width="1.5"/></svg><span>info@meadowcrestcourier.example</span></li>
</ul>
<p class="copyright abs" style="color:#fff">© Copyright Meadowcrest Courier 2018. All rights reserved.</p>

</body>
</html>
```